We need a business card for our gym. We are a PowerCore affiliate in Decatur Georgie established 2008. Our company name is Rally Functional Fitness. PowerCore Building Prime Fitness. Instagram and website is @rallygym. Hashtags we use #rallywithheart #madetorally We want something similar to the the black and neon green design attached but a different color scheme. No neon colors. Are company colors are the same as the blue and white card attached. We are open to ideas as far as colors however - just no neon.

Contact Information for Business Card

Rally Functional Fitness
472 Halvern Drive
Decatur GA 30041
Phone 404.555.0187 Website www.rallygym.example

Font styles to use
Other font styles liked:
• Futura Extra Bold Condensed

Colors

Designer to choose colors to be used in the design.

Requirements
Must have
• Our primary font we typically use for our name is Futura Extra Bold Condensed
Nice to have
• I attached a card from that is black and neon green from Zorva that we would like something similar. The blue and white is more similar to our colors. We also use have used black and white in the past. We use the chevrons as out logo. We are a PowerCore affiliate so I included a logo from them as well that may or may not be used on the card. Our instagram is @rallygym hashtags #madetorally #rallywithheart
Should not have
• No neon colors

```html
<!DOCTYPE html>
<html lang="en">
<head>
<meta charset="UTF-8">
<title>Rally Functional Fitness — Business Card</title>
<link href="https://fonts.googleapis.com/css2?family=Anton&family=Montserrat:wght@400;500&display=swap" rel="stylesheet">
<style>
  :root {
    --stage: #3a3a3c;
    --card: #262627;
    --card-edge: #2f2f30;
    --sky: #8dd1f3;
    --white: #f4f4f4;
    --muted: #dcdcdc;
  }
  * { margin: 0; padding: 0; box-sizing: border-box; }
  html, body {
    width: 1200px;
    height: 901px;
    overflow: hidden;
    background: var(--stage);
  }
  .stage {
    position: relative;
    width: 1200px;
    height: 901px;
  }
  .card {
    position: absolute;
    left: 290px;
    width: 620px;
    height: 354px;
    background: linear-gradient(135deg, var(--card-edge) 0%, var(--card) 60%);
    box-shadow: 0 14px 30px rgba(0,0,0,0.45);
    overflow: hidden;
  }
  .card--front { top: 70px; }
  .card--back { top: 470px; }

  .wordmark {
    font-family: "Anton", "Oswald", sans-serif;
    color: var(--sky);
    text-transform: uppercase;
    text-align: center;
    line-height: 0.95;
  }
  .wordmark__name { display: block; font-size: 96px; letter-spacing: 2px; }
  .wordmark__tag { display: block; font-size: 34px; letter-spacing: 1px; }

  .card--front .wordmark {
    position: absolute;
    left: 0; right: 0;
    top: 92px;
  }

  .card--back .wordmark {
    position: absolute;
    right: 44px;
    top: 40px;
  }
  .card--back .wordmark__name { font-size: 70px; }
  .card--back .wordmark__tag { font-size: 25px; }

  .holder {
    position: absolute;
    left: 40px;
    top: 132px;
  }
  .holder__name {
    font-family: "Anton", "Oswald", sans-serif;
    color: var(--sky);
    font-size: 32px;
    letter-spacing: 2px;
    text-transform: uppercase;
    line-height: 1;
  }
  .holder__role {
    font-family: "Montserrat", sans-serif;
    color: var(--muted);
    font-size: 17px;
    letter-spacing: 1px;
    margin-top: 6px;
  }
  .divider {
    position: absolute;
    left: 40px;
    right: 70px;
    top: 208px;
    height: 2px;
    background: var(--sky);
  }
  .contact {
    position: absolute;
    left: 40px;
    top: 232px;
    list-style: none;
    font-family: "Montserrat", sans-serif;
    color: var(--white);
    font-size: 19px;
  }
  .contact__item {
    display: flex;
    align-items: center;
    gap: 10px;
    margin-bottom: 8px;
  }
  .contact__icon { width: 17px; height: 17px; flex: none; }
  .address {
    position: absolute;
    right: 70px;
    bottom: 34px;
    font-family: "Montserrat", sans-serif;
    font-style: normal;
    color: var(--white);
    font-size: 20px;
    line-height: 1.3;
    text-align: right;
    letter-spacing: 0.5px;
  }
</style>
</head>
<body>
<main class="stage">
  <section class="card card--front" aria-label="Card front">
    <h1 class="wordmark">
      <span class="wordmark__name">Rally</span>
      <span class="wordmark__tag">Functional Fitness</span>
    </h1>
  </section>

  <section class="card card--back" aria-label="Card back">
    <div class="wordmark">
      <span class="wordmark__name">Rally</span>
      <span class="wordmark__tag">Functional Fitness</span>
    </div>

    <div class="holder">
      <p class="holder__name">Daniel Harrow</p>
      <p class="holder__role">EXPERT COACHES</p>
    </div>

    <div class="divider"></div>

    <ul class="contact">
      <li class="contact__item">
        <svg class="contact__icon" viewBox="0 0 24 24" aria-hidden="true">
          <path fill="var(--sky)" d="M6.6 10.8a15.2 15.2 0 0 0 6.6 6.6l2.2-2.2a1 1 0 0 1 1-.25 11.4 11.4 0 0 0 3.6.57 1 1 0 0 1 1 1V20a1 1 0 0 1-1 1A17 17 0 0 1 3 4a1 1 0 0 1 1-1h3.5a1 1 0 0 1 1 1c0 1.25.2 2.45.57 3.57a1 1 0 0 1-.25 1z"/>
        </svg>
        <span>404.555.0187</span>
      </li>
      <li class="contact__item">
        <svg class="contact__icon" viewBox="0 0 24 24" aria-hidden="true">
          <circle cx="12" cy="12" r="9.5" fill="none" stroke="var(--sky)" stroke-width="2"/>
          <path fill="none" stroke="var(--sky)" stroke-width="1.6" d="M2.5 12h19M12 2.5c3 3 3 16 0 19M12 2.5c-3 3-3 16 0 19"/>
        </svg>
        <span>www.rallygym.example</span>
      </li>
    </ul>

    <address class="address">
      472 Halvern Drive<br>
      Decatur GA 30041
    </address>
  </section>
</main>
</body>
</html>
```